Design and Renovation Company Luxury Business Card

I want to create a luxury business card for a Design and Renovation Firm . We will use our current logo. The company name is 528BUILDA. We do not want anything standard. We need a very unique concept.
Please see uploaded inspiration. I really like the textured paper option. I would like the card to be thick with debossing, and/or embossing options. The logo has orange in it but I would like to see the card with and without the orange. I think the orange may make the company feel less high-end. The goal is to elevate the logo not match its vibe per se of the logo. We want something very unique, not standard at all!
I would like a space for :
Logo,
Name,
Position,
Email,
Office number,
Website Address,
Business Address,
Thank you!
Have fun!
Target Market(s)
Home owners Age 35 +
Industry/Entity Type
Design and Renovation
Contact Information for Business Card
Logo, Name, Position, Email, Office number, Website Address, Business Address,.
Colors
Designer to choose colors to be used in the design.
Requirements
Must have
- A luxury designer feel. Must be black or dark grey but open to other luxury ideas.
Nice to have
- Gold, silver, black embossing or debossing. Textured paper design.
Should not have
- A cheap look and feel.

```html
<!DOCTYPE html>
<html lang="en">
<head>
<meta charset="utf-8">
<title>528BUILDA Business Card</title>
<link href="https://fonts.googleapis.com/css2?family=Saira:wght@400;700&display=swap" rel="stylesheet">
<style>
  :root {
    --backdrop: #262626;
    --card: #313131;
    --card-edge: #3a3a3a;
    --accent: #f39321;
    --text-light: #e6e6e6;
    --text-mid: #9a9a9a;
    --text-dim: #1c1c1c;
  }
  * { box-sizing: border-box; margin: 0; padding: 0; }
  html, body {
    width: 1200px; height: 799px; overflow: hidden;
    background: var(--backdrop);
    font-family: "Saira", sans-serif;
  }
  .spread {
    position: relative; width: 1200px; height: 799px;
    display: flex; align-items: center; justify-content: center; gap: 50px;
  }
  .card {
    position: relative; width: 530px; height: 303px;
    background: var(--card);
    border: 1px solid var(--card-edge);
    box-shadow: 0 18px 40px rgba(0,0,0,.45);
  }
  /* Front */
  .card--front {
    display: flex; flex-direction: column; align-items: center; justify-content: center; gap: 10px;
  }
  .company-name {
    font-size: 40px; font-weight: 400; line-height: 1;
    color: var(--text-dim);
  }
  .company-line {
    font-size: 13px; font-weight: 400; color: var(--text-dim);
  }
  /* Back */
  .card--back { display: flex; align-items: center; padding: 0 34px 0 38px; }
  .back-brand { width: 190px; display: flex; justify-content: center; }
  .back-brand .company-name { font-size: 24px; color: var(--text-mid); }
  .divider { width: 1px; height: 160px; background: var(--accent); margin: 0 26px 0 12px; }
  .contact { flex: 1; }
  .person-name { font-size: 24px; font-weight: 700; letter-spacing: 1.5px; color: var(--text-light); line-height: 1.1; }
  .person-role { font-size: 13px; color: var(--accent); margin-bottom: 14px; }
  .contact-list { list-style: none; }
  .contact-list li {
    display: flex; gap: 9px; align-items: flex-start;
    font-size: 11.5px; line-height: 1.45; color: var(--text-light); margin-bottom: 3px;
  }
  .contact-list svg { flex: none; width: 12px; height: 12px; margin-top: 3px; fill: var(--accent); }
</style>
</head>
<body>
<main class="spread">
  <section class="card card--front" aria-label="Card front">
    <span class="company-name">528BUILDA</span>
    <span class="company-line">Design and Renovation Firm</span>
  </section>

  <section class="card card--back" aria-label="Card back">
    <div class="back-brand">
      <span class="company-name">528BUILDA</span>
    </div>
    <div class="divider"></div>
    <div class="contact">
      <h1 class="person-name">ADRIAN VALE</h1>
      <p class="person-role">Founder &amp; CEO</p>
      <ul class="contact-list">
        <li>
          <svg viewBox="0 0 12 12"><path d="M6 0a4 4 0 0 0-4 4c0 3 4 8 4 8s4-5 4-8a4 4 0 0 0-4-4zm0 5.6A1.6 1.6 0 1 1 6 2.4a1.6 1.6 0 0 1 0 3.2z"/></svg>
          <span>87 Harrow Lane, Suite 4, Cityview<br>Stateland, Country, 00000</span>
        </li>
        <li>
          <svg viewBox="0 0 12 12"><path d="M2.5 0.5l2 2.4-1.2 1.4c.8 1.7 2.1 3 3.8 3.8l1.4-1.2 2.4 2-1.3 2.3C4.4 11 1 7.6.2 2.6z"/></svg>
          <span>+1 5550 142 736</span>
        </li>
        <li>
          <svg viewBox="0 0 12 12"><path d="M0 2h12v8H0zm1 1l5 3.6L11 3z" fill-rule="evenodd"/></svg>
          <span>hello@528builda-studio.com</span>
        </li>
        <li>
          <svg viewBox="0 0 12 12"><circle cx="6" cy="6" r="5.5"/><path d="M3 4h6M3 8h6M6 .5v11" stroke="#313131" stroke-width="1"/></svg>
          <span>528builda-studio.com</span>
        </li>
      </ul>
    </div>
  </section>
</main>
</body>
</html>
```